Larkspur Talent IT Recruiting firm needs a business card design for Recruiters, Sourcers, and Account

We need business cards that allow us to change all contact info, names, titles (Recruiter, Sourcer, Account Manager, Director, CEO, etc) per person since we have three offices, in three cities, Phoenix, Austin, and Las Vegas. We do recruiting and contractors for IT positions (Developers, Architects, Software Engineers, Security Engineers, Help Desk, DBAs, PMs, Scrum Masters, etc.) Our client companies are very diverse from Meridian 100 to silicone Valley type start-ups.

So, while we what hip, techie, and quirky, it still needs to be professional. Primary color we use is blue, with silver as a secondary color.

Target Market(s)

IT, Technology

Industry/Entity Type

Business

Contact Information for Business Card

Company name: Larkspur Talent, Inc.
Website: www.larkspurtalent.example
Logos for Careerloop, Blipster, and Myriada

Name, Title, Office Number, Cell Number, email

Font styles to use
Serif
Sans Serif

Colors
0455a3
d5d5d5

Requirements
Nice to have
• The grey I selected below is not necessary - but, would like silver included. I included a card design (File 3: LTI early trial example.jpg) that I had started on. It's very rough, and not quite what we're looking for, but what we did like is the logo, big, maybe a bit faded, off center, goes out of frame, etc. Still looking for other ideas - you are the pros! But, just an idea of a design element we liked.

```html
<!DOCTYPE html>
<html lang="en">
<head>
<meta charset="utf-8">
<title>Larkspur Talent – Business Card</title>
<link rel="stylesheet" href="https://fonts.googleapis.com/css2?family=Marcellus&family=Source+Sans+3:wght@400;600&display=swap">
<style>
  :root {
    --backdrop: #1b1b1b;
    --paper: #ffffff;
    --ink: #1f1f1f;
    --brand-blue: #0455a3;
    --brand-blue-light: #0a8ad6;
    --silver: #d5d5d5;
    --slate: #555555;
    --on-dark: #ffffff;
  }
  * { box-sizing: border-box; margin: 0; padding: 0; }
  html, body {
    width: 1200px; height: 907px; overflow: hidden;
    background: var(--backdrop);
  }
  .stage { position: relative; width: 1200px; height: 907px; }
  .card {
    position: absolute; left: 300px; width: 600px; height: 343px; overflow: hidden;
    box-shadow: 0 6px 18px rgba(0,0,0,.55);
  }
  .card--front { top: 98px; background: var(--paper); }
  .card--back  { top: 475px; background: var(--slate); }

  .wave { position: absolute; inset: 0; width: 600px; height: 343px; }

  .brand {
    position: absolute; left: 0; right: 0; text-align: center;
    font-family: "Marcellus", serif;
  }
  .brand__name {
    display: inline-flex; align-items: center; gap: 12px;
    font-size: 40px; letter-spacing: 3px; line-height: 1;
  }
  .brand__dot { width: 30px; height: 30px; border-radius: 50%; flex: none; }
  .brand__sub { display: block; font-size: 26px; letter-spacing: 5px; margin-top: 4px; text-align: right; width: 300px; margin-left: auto; margin-right: auto; }
  .brand__tagline { display: block; font-size: 15px; letter-spacing: 1.8px; margin-top: 12px; }

  .card--front .brand { top: 40px; color: var(--brand-blue); }
  .card--front .brand__dot { background: var(--brand-blue); }
  .card--front .brand__tagline { color: var(--ink); }

  .card--back .brand { top: 110px; color: var(--on-dark); }
  .card--back .brand__dot { background: var(--on-dark); }

  .person {
    position: absolute; right: 370px; top: 238px; text-align: right;
    font-family: "Source Sans 3", sans-serif; color: var(--on-dark);
  }
  .person__name { font-size: 22px; line-height: 1.1; }
  .person__role { font-size: 15px; margin-top: 6px; }
  .divider { position: absolute; left: 246px; top: 226px; width: 1px; height: 74px; background: rgba(255,255,255,.75); }

  .contacts {
    position: absolute; left: 264px; top: 218px; list-style: none;
    font-family: "Source Sans 3", sans-serif; font-size: 15px; color: var(--on-dark);
  }
  .contacts li { display: flex; align-items: center; gap: 8px; height: 22.5px; }
  .contacts svg { width: 14px; height: 14px; flex: none; }

  .social {
    position: absolute; left: 0; right: 0; top: 292px;
    display: flex; justify-content: center; gap: 16px; list-style: none;
    font-family: "Source Sans 3", sans-serif; font-size: 13px; font-weight: 600; color: var(--silver);
  }
  .social li { display: flex; align-items: center; gap: 5px; }
  .social li::before { content: ""; width: 10px; height: 10px; background: var(--brand-blue-light); }
</style>
</head>
<body>
<main class="stage">
  <section class="card card--front" aria-label="Card front">
    <svg class="wave" viewBox="0 0 600 343" aria-hidden="true">
      <defs>
        <radialGradient id="blueField" cx="0.55" cy="0.75" r="0.7">
          <stop offset="0" stop-color="var(--brand-blue-light)"/>
          <stop offset="1" stop-color="var(--brand-blue)"/>
        </radialGradient>
      </defs>
      <path d="M0 146 C120 192 250 184 360 172 C460 162 540 160 600 190 L600 343 L0 343Z" fill="var(--slate)"/>
      <path d="M0 166 C120 200 250 192 360 180 C460 172 540 174 600 196 L600 343 L0 343Z" fill="var(--paper)"/>
      <path d="M0 170 C120 204 250 196 360 184 C460 176 540 178 600 200 L600 343 L0 343Z" fill="url(#blueField)"/>
    </svg>

    <div class="brand">
      <span class="brand__name"><span class="brand__dot"></span>LARKSPUR</span>
      <span class="brand__sub">TALENT</span>
      <span class="brand__tagline">MATCHING TALENT TO TECH</span>
    </div>

    <div class="person">
      <p class="person__name">Daniel Reyes</p>
      <p class="person__role">Manager</p>
    </div>
    <div class="divider"></div>

    <ul class="contacts">
      <li>
        <svg viewBox="0 0 16 16" fill="#fff"><path d="M4 1l3 3-1.6 1.8a9 9 0 0 0 4.8 4.8L12 9l3 3-2 2.5C7 14 2 9 1.5 3Z"/></svg>
        555-014-2290
      </li>
      <li>
        <svg viewBox="0 0 16 16" fill="none" stroke="#fff" stroke-width="1.6"><rect x="4" y="1" width="8" height="14" rx="1.5"/><line x1="6" y1="12" x2="10" y2="12"/></svg>
        555-017-6634
      </li>
      <li>
        <svg viewBox="0 0 16 16" fill="none" stroke="#fff" stroke-width="1.5"><rect x="1" y="3.5" width="14" height="9"/><path d="M1 3.5l7 5 7-5"/></svg>
        info@larkspurtalent.example
      </li>
      <li>
        <svg viewBox="0 0 16 16" fill="none" stroke="#fff" stroke-width="1.2"><circle cx="8" cy="8" r="6.5"/><ellipse cx="8" cy="8" rx="3" ry="6.5"/><line x1="1.5" y1="8" x2="14.5" y2="8"/></svg>
        www.larkspurtalent.example
      </li>
    </ul>
  </section>

  <section class="card card--back" aria-label="Card back">
    <div class="brand">
      <span class="brand__name"><span class="brand__dot"></span>LARKSPUR</span>
      <span class="brand__sub">TALENT</span>
      <span class="brand__tagline">MATCHING TALENT TO TECH</span>
    </div>
    <ul class="social">
      <li>Careerloop</li>
      <li>Blipster</li>
      <li>Myriada</li>
    </ul>
  </section>
</main>
</body>
</html>
```